Food Packaging Carton Designs

We require a professional carton design system for our packaging products under the heading "DWR" (cartons that hold food-service containers such as cups, lids, napkins, trays).
The design must:
- Compete visually with large packaging brands.
- Be consistent across multiple SKUs and carton sizes.
- Present key specs clearly (brand, product name, dimensions, quantity, SKU code, barcode).
- Comply with Australian requirements for packaging, barcodes, environmental claims, and trade measurement.
- Be supplied in factory-ready print files that can go straight to manufacturers.
- Use one colour/style for the brand name (DWR), but colour code the product families or have some visual differentiation for each to make it easy to spot and pick in the warehouse.
Minimum Content required on boxes:
- Brand Name (top and prominent)
- Product family (e.g. Napkins)
- Product name (e.g. KR Vela Napkin)
- Product code (e.g. HNV417)
- Dimensions (e.g. 310x300x180mm)
- quantity (e.g. 250pcs)
Side/end panels
- Repeat brand, product family/name/code
- Orientation arrows.
- Space for logistics labels.
Creative direction
- Clean, modern, high-contrast typography for storeroom and warehouse visibility.
- Consistent brand framework with colour or pattern variants by product family.
- Large numerals for size/capacity and product names/codes.
- Clear fields for shipping/barcode labels.
- Take inspiration from larger competitors (examples of their cartons attached)
Technical print setup
- Vector artwork only (AI or EPS).
- Press-ready PDF/X with 3–5 mm bleed and crop marks.
- CMYK colour mode, spot colours specified if used.
- Raster images at 300 dpi at final size.
- Fonts outlined in PDFs but editable AI with live text provided.
- Separate layers for dielines, varnish, foil, emboss, white plates.
Deliverables
- Design system (templates/style sheet) that can easily be updated as we change/update product range.
- Final designs for key product family range which includes: Haulies (these are brown bags with twist handles), Paper Bowls, Sugarcane Clams, Plates, Rectangle Containers, Napkins.
- Print-ready PDF/X files for factory printing.
- Editable AI/EPS files with packaged links.
- Colour palette/style sheet.
- 3D mockups and flat artwork on dielines.
Other:
- our website is www.dorvantic.com.au
- brand name is "DWR"
Restaurants, cafes, bars, clubs, schools, coffee shops/vans
Wholesale packaging

```html
<!DOCTYPE html>
<html lang="en">
<head>
<meta charset="utf-8">
<title>DWR Sugarcane Clams Carton</title>
<link href="https://fonts.googleapis.com/css2?family=Montserrat:wght@500;600;700;800;900&family=Cormorant+Garamond:wght@600&display=swap" rel="stylesheet">
<style>
  :root {
    --bg: #f3f3f3;
    --kraft: #caa27e;
    --kraft-shade: #b98f6b;
    --green: #0b5245;
    --ink: #1f1f1f;
    --ink-soft: #3a3a3a;
  }
  * { box-sizing: border-box; margin: 0; padding: 0; }
  html, body { width: 1200px; height: 908px; overflow: hidden; }
  body { background: var(--bg); font-family: "Montserrat", sans-serif; color: var(--ink); position: relative; }

  .carton { position: absolute; top: 200px; left: 120px; display: flex; height: 520px; }

  /* End panel */
  .end-panel { width: 250px; height: 520px; background: var(--kraft-shade); position: relative; overflow: hidden; }
  .end-panel .wave { position: absolute; left: 0; bottom: 0; }
  .spec-list { position: absolute; top: 40px; left: 22px; font-size: 10px; line-height: 1.55; color: var(--ink-soft); font-weight: 500; }
  .spec-list p.gap { margin-top: 12px; }
  .handling-icons { position: absolute; top: 260px; left: 40px; display: flex; gap: 14px; align-items: flex-end; }
  .end-badges { position: absolute; bottom: 40px; left: 14px; display: flex; gap: 8px; }
  .end-badges span { display: flex; flex-direction: column; align-items: center; gap: 3px; font-size: 6px; color: var(--kraft); }
  .end-badges i { width: 16px; height: 16px; border-radius: 50%; border: 1.5px solid var(--kraft); display: block; }
  .end-brand { position: absolute; bottom: 42px; right: 16px; font-family: "Cormorant Garamond", serif; font-size: 14px; color: var(--kraft); letter-spacing: 1px; }

  /* Front panel */
  .front-panel { width: 760px; height: 520px; background: var(--kraft); position: relative; overflow: hidden; }
  .front-panel .wave { position: absolute; left: 0; bottom: 0; }
  .brand-lockup { position: absolute; top: 42px; left: 40px; display: flex; align-items: center; gap: 10px; color: var(--ink-soft); }
  .brand-lockup .dot { width: 22px; height: 22px; border-radius: 50%; border: 2px solid var(--ink-soft); }
  .brand-lockup .name { font-family: "Cormorant Garamond", serif; font-size: 22px; letter-spacing: 1.5px; line-height: 1; border-left: 1px solid var(--ink-soft); padding-left: 10px; }
  .brand-lockup .name small { display: block; font-size: 9px; letter-spacing: 1.2px; margin-top: 2px; }
  .site-url { position: absolute; top: 74px; right: 40px; font-size: 19px; font-weight: 700; color: var(--green); }
  .range-name { position: absolute; top: 100px; left: 34px; font-size: 116px; font-weight: 900; color: var(--green); line-height: 1; letter-spacing: 2px; }
  .product-name { position: absolute; top: 222px; left: 38px; font-size: 50px; font-weight: 700; line-height: 1.05; color: var(--ink); }
  .product-family { position: absolute; top: 336px; left: 40px; font-size: 24px; font-weight: 500; color: var(--ink); }
  .product-visual { position: absolute; top: 286px; left: 320px; width: 170px; height: 78px; border-radius: 14px 14px 22px 22px; background: linear-gradient(180deg, #d6b596, #bd9572); }
  .cert-badges { position: absolute; top: 122px; right: 70px; display: flex; gap: 34px; align-items: flex-start; }
  .cert-plain { width: 78px; height: 132px; border: 1.5px solid var(--green); border-radius: 8px; }
  .cert-round { display: flex; flex-direction: column; align-items: center; gap: 10px; }
  .cert-round i { width: 62px; height: 62px; border-radius: 50%; border: 2px solid var(--green); display: block; }
  .cert-round span { font-size: 7px; color: var(--green); text-align: center; font-weight: 600; line-height: 1.3; }
  .product-code { position: absolute; bottom: 54px; right: 38px; font-size: 70px; font-weight: 700; color: var(--kraft); letter-spacing: 1px; line-height: 1; }
  .claims { position: absolute; bottom: 28px; left: 44px; display: flex; gap: 22px; }
  .claims span { display: flex; flex-direction: column; align-items: center; gap: 8px; font-size: 9px; font-weight: 600; color: var(--kraft); width: 76px; }
  .claims i { width: 38px; height: 38px; border-radius: 50%; border: 2px solid var(--kraft); display: block; }
</style>
</head>
<body>
  <main class="carton">
    <section class="end-panel">
      <svg class="wave" width="250" height="520" viewBox="0 0 250 520">
        <path d="M0 340 C 60 380, 150 390, 250 370 L250 520 L0 520 Z" fill="var(--green)"/>
      </svg>
      <div class="spec-list">
        <p>DWR</p>
        <p>Product: Sugarcane Clams</p>
        <p>Code: SCN218</p>
        <p class="gap">Ctn Qty: 400 pcs (4 x 100's)</p>
        <p>Gross Wt: (to confirm from supplier)</p>
        <p>Dimensions: 150 x 150 x 80 mm</p>
        <p>Run Date: 01/02/2025</p>
        <p>Batch No: ___</p>
      </div>
      <div class="handling-icons">
        <svg width="26" height="40" viewBox="0 0 26 40" aria-label="Recyclable"><circle cx="13" cy="20" r="11" fill="none" stroke="var(--ink)" stroke-width="3"/></svg>
        <svg width="34" height="58" viewBox="0 0 34 58" aria-label="This way up">
          <g fill="var(--ink)"><path d="M9 2 L2 14 H7 V42 H11 V14 H16 Z"/><path d="M25 2 L18 14 H23 V42 H27 V14 H32 Z"/><rect x="2" y="50" width="30" height="5"/></g>
        </svg>
        <svg width="34" height="58" viewBox="0 0 34 58" aria-label="Keep dry">
          <g fill="none" stroke="var(--ink)" stroke-width="3"><path d="M3 26 Q17 6 31 26 Z" fill="var(--ink)"/><path d="M17 26 V48 Q17 54 12 52"/></g>
        </svg>
      </div>
      <div class="end-badges">
        <span><i></i>Earth-friendly</span>
        <span><i></i>Compostable</span>
        <span><i></i>Biodegradable</span>
      </div>
      <div class="end-brand">Dorvantic</div>
    </section>

    <section class="front-panel">
      <svg class="wave" width="760" height="520" viewBox="0 0 760 520">
        <path d="M0 392 C 180 382, 520 372, 640 340 C 700 322, 735 300, 760 282 L760 520 L0 520 Z" fill="var(--green)"/>
      </svg>
      <div class="brand-lockup"><span class="dot"></span><span class="name">DORVANTIC<small>FOOD-SERVICE PACKAGING</small></span></div>
      <div class="site-url">www.dorvantic.com.au</div>
      <h1 class="range-name">DWR</h1>
      <h2 class="product-name">Sugarcane<br>Clams</h2>
      <p class="product-family">Containers</p>
      <div class="product-visual" role="img" aria-label="Line drawing of an open sugarcane clamshell container"></div>
      <div class="cert-badges">
        <div class="cert-plain"></div>
        <div class="cert-round"><i></i><span>Product Made with<br>100% Recycled Fiber</span></div>
      </div>
      <div class="claims">
        <span><i></i>Earth-friendly</span>
        <span><i></i>Compostable</span>
        <span><i></i>Biodegradable</span>
      </div>
      <div class="product-code">SCN218</div>
    </section>
  </main>
</body>
</html>
```